Valdane Companies Business Card Design

We need a new business card for our Private Equity Real Estate Development firm, “Valdane” and our EB-5 regional center “Thornmere Regional Center” on one card. We prefer a design that is simple, elegant, and represents the luxury products we design and build as well as the financial security and stability our successful history has produced. We are an industry leader in our field and 3rd generation family business that has evolved into an institutional quality investment platform. Considered design size is standard business card dimensions (3.5 x 2 inches with an additional 1/8 inch space for design elements or backgrounds that extend beyond the finished size of your piece.

Target Market(s)

• High net worth individuals
• Highly skilled technical workers and physicians in the US seeking investment-based immigration opportunities
• Sophisticated private equity investors
• Intermediary partners include domestic attorneys and investment brokers, as well as international agent networks
• US real estate developers

Industry/Entity Type

Finance

Contact Information for Business Card

(Providing placeholder info for personal information, please design for longer character spaces, longer names and addresses etc..)
• Logo for Valdane
• Logo for Thornmere Regional Center
• Full name: Marcus Valdane
• Job title: CEO
• Email address: mvaldane@valdanecompanies.com
• Cell phone number: +1.555.314.2287
• Office number +1.555.628.4410
• Office address: Larkfield Court 5, 4817 Vista Orilla, San Ramon, CA.
• Website: www.valdanecompanies.com

Font styles to use
Serif
Sans Serif

Colors
ec1f27
ffffff
000000

Requirements
Must have
• • Logo for Valdane
• • Logo for Thornmere Regional Center
• - Use rounded corners
• (See .ai file included for logos)
Nice to have
• • Simple, elegant design
• • Aesthetically compatible with our website design (www.valdanecompanies.com)
• • Color palette including but not limited to white, black, and red (as per logos)
Should not have
• - Not too much red color
• - Do not stack both logos on top of each other

```html
<!DOCTYPE html>
<html lang="en">
<head>
<meta charset="utf-8">
<title>Valdane Companies Business Card</title>
<link rel="stylesheet" href="https://fonts.googleapis.com/css2?family=Cinzel:wght@600&family=Oswald:wght@500&family=Work+Sans:wght@400&display=swap">
<style>
  :root {
    --stage: #2a2a2a;
    --card-black: #0f0f10;
    --card-white: #ffffff;
    --brand-red: #b3122a;
    --ink: #3a3a3a;
    --ink-soft: #555555;
    --rule: #4a4a4a;
    --white: #ffffff;
  }
  * { box-sizing: border-box; margin: 0; padding: 0; }
  html, body { width: 1200px; height: 800px; overflow: hidden; }
  body {
    background: var(--stage);
    display: flex;
    align-items: center;
    justify-content: center;
    gap: 40px;
    font-family: "Work Sans", sans-serif;
  }
  .card {
    position: relative;
    width: 540px;
    height: 309px;
    border-radius: 18px;
    overflow: hidden;
  }

  /* Front: regional center */
  .card--front { background: var(--card-black); }
  .brand-small {
    position: absolute;
    top: 34px;
    right: 36px;
    display: flex;
    align-items: center;
    gap: 8px;
    font-family: "Cinzel", serif;
    font-weight: 600;
    font-size: 12px;
    letter-spacing: 1.5px;
    color: var(--brand-red);
  }
  .brand-small .mark { width: 10px; height: 10px; background: var(--brand-red); }
  .brand-large {
    position: absolute;
    left: 60px;
    top: 50%;
    transform: translateY(-50%);
    display: flex;
    align-items: center;
    gap: 16px;
    font-family: "Cinzel", serif;
    font-weight: 600;
    font-size: 26px;
    letter-spacing: 2px;
    color: var(--white);
  }
  .brand-large .mark { width: 22px; height: 22px; background: var(--white); }

  /* Back: contact */
  .card--back { background: var(--card-white); }
  .company {
    position: absolute;
    left: 40px;
    top: 112px;
    width: 180px;
    display: flex;
    align-items: center;
    gap: 10px;
    font-family: "Cinzel", serif;
    font-weight: 600;
    font-size: 17px;
    letter-spacing: 1px;
    color: var(--ink);
  }
  .company .mark { width: 12px; height: 12px; background: var(--ink); flex: none; }
  .divider {
    position: absolute;
    left: 240px;
    top: 54px;
    width: 1.5px;
    height: 140px;
    background: var(--rule);
  }
  .contact {
    position: absolute;
    left: 266px;
    top: 50px;
  }
  .person-name {
    font-family: "Oswald", sans-serif;
    font-weight: 500;
    font-size: 24px;
    letter-spacing: 0.3px;
    color: var(--ink);
    text-transform: uppercase;
  }
  .person-title {
    margin-top: 4px;
    font-size: 12px;
    color: var(--ink);
    letter-spacing: 0.5px;
  }
  .details { list-style: none; margin-top: 14px; }
  .details li {
    display: flex;
    align-items: center;
    gap: 9px;
    font-size: 12.5px;
    line-height: 19px;
    color: var(--ink-soft);
  }
  .details svg { width: 9px; height: 9px; flex: none; }
  .address {
    position: absolute;
    left: 0;
    right: 0;
    bottom: 30px;
    text-align: center;
    font-size: 12px;
    letter-spacing: 1.4px;
    color: var(--ink-soft);
  }
</style>
</head>
<body>
  <section class="card card--front" aria-label="Card front">
    <div class="brand-small"><span class="mark"></span>THORNMERE REGIONAL CENTER</div>
    <div class="brand-large"><span class="mark"></span>THORNMERE REGIONAL CENTER</div>
  </section>

  <section class="card card--back" aria-label="Card back">
    <div class="company"><span class="mark"></span>VALDANE CAPITAL</div>
    <div class="divider"></div>
    <div class="contact">
      <h1 class="person-name">Marcus Valdane</h1>
      <p class="person-title">CEO</p>
      <ul class="details">
        <li>
          <svg viewBox="0 0 10 10" aria-hidden="true"><path d="M2 1 L4 1 L4.6 3 L3.4 4 Q4.5 6 6 6.6 L7 5.4 L9 6 L9 8 Q9 9 8 9 Q1 8.5 1 2 Q1 1 2 1Z" fill="#555"/></svg>
          +1.555.314.2287
        </li>
        <li>
          <svg viewBox="0 0 10 10" aria-hidden="true"><rect x="2.5" y="0.5" width="5" height="9" rx="1" fill="none" stroke="#555"/><circle cx="5" cy="7.8" r="0.6" fill="#555"/></svg>
          +1.555.628.4410
        </li>
        <li>
          <svg viewBox="0 0 10 10" aria-hidden="true"><rect x="0.5" y="2" width="9" height="6" fill="none" stroke="#555"/><path d="M0.5 2 L5 5.5 L9.5 2" fill="none" stroke="#555"/></svg>
          mvaldane@valdanecompanies.com
        </li>
        <li>
          <svg viewBox="0 0 10 10" aria-hidden="true"><circle cx="5" cy="5" r="4.3" fill="none" stroke="#555"/><ellipse cx="5" cy="5" rx="1.8" ry="4.3" fill="none" stroke="#555"/><path d="M0.7 5 H9.3" stroke="#555"/></svg>
          www.valdanecompanies.com
        </li>
      </ul>
    </div>
    <p class="address">Larkfield Court 5, 4817 Vista Orilla, San Ramon, CA.</p>
  </section>
</body>
</html>
```